Marwick Law Letterhead

We need a new letterhead design for a Law Firm. The address for the law firm is 1475 Calloway Street, Suite 210, Houston, Texas 77041. Phone Number: 832-361-9027; Fax Number: 832-614-7359. The logo is uploaded to the project.

```html
<!DOCTYPE html>
<html lang="en">
<head>
<meta charset="utf-8">
<title>Marwick Law Letterhead</title>
<link rel="stylesheet" href="https://fonts.googleapis.com/css2?family=Figtree:wght@400;600&display=swap">
<style>
  :root{
    --backdrop:#e8e8e8;
    --paper:#ffffff;
    --navy:#1e3164;
    --red:#e21b23;
    --red-deep:#7c0610;
    --ink:#2b2b2b;
    --on-red:#ffffff;
  }
  *{box-sizing:border-box;margin:0;padding:0}
  html,body{width:1154px;height:1200px;overflow:hidden;background:var(--backdrop)}
  body{font-family:"Figtree",Arial,sans-serif;color:var(--ink)}
  .letterhead{
    position:absolute;left:162px;top:20px;width:830px;height:1160px;
    background:var(--paper);overflow:hidden;
    box-shadow:0 4px 18px rgba(0,0,0,.18);
  }
  .brand{position:absolute;left:32px;top:96px;display:flex;align-items:center;gap:14px}
  .brand-mark{width:50px;height:50px;border-radius:50%;background:var(--navy)}
  .brand-name{font-family:"Figtree",Arial,sans-serif;font-weight:600;font-size:34px;color:var(--navy);letter-spacing:.5px}
  .recipient{position:absolute;left:31px;top:277px;font-size:14px;line-height:20.6px}
  .letter-body{position:absolute;left:33px;top:364px;width:769px;font-size:14px;line-height:20.6px;text-align:justify}
  .letter-body p{margin-bottom:20.6px}
  .footer-wave{position:absolute;left:0;top:0;width:830px;height:1160px}
  .contact{position:absolute;left:597px;top:1023px;color:var(--on-red);font-size:14.5px;line-height:18px}
  .contact-address{margin-bottom:10px}
  .contact-line{display:flex;align-items:center;gap:11px;height:21px}
  .contact-line svg{width:11px;height:11px;fill:var(--on-red)}
</style>
</head>
<body>
<main class="letterhead">
  <header class="brand">
    <span class="brand-mark"></span>
    <span class="brand-name">Marwick Law</span>
  </header>

  <address class="recipient" style="font-style:normal">
    Mr/s<br>First Name and Last Name<br>Company Name<br>Address
  </address>

  <section class="letter-body">
    <p>Lorem ipsum dolor sit amet,consectetur adipiscing sed do eiusmod tempor incididunt laboreet dolore magna aliqua.Ut enim ad minim.veniam, quis nostrud exercitation ullamco laboris nisi ut aliquip exea commodo consequat.Lorem ipsum dolor sit amet,consectetur adipiscing sed do eiusmod tempor incididunt.labore et dolore magna aliqua. Ut enim</p>
    <p>Lorem ipsum dolor sit amet, consectetur adipiscing sed do eiusmod tempor incididunt labore et dolore magna aliqua. Ut enim ad minim veniam, quis nostrud exercitation ullamco laboris nisi ut aliquip exea commodo consequat.Duis aute irure dolor in reprehenderit in voluptate velit esse cillum irure dolor in reprehenderit in voluptate velit esse irure</p>
    <p>Lorem ipsum dolor sit amet, consectetur adipiscing sed do eiusmod tempor incididunt labore et dolore magna aliqua. consequat. Duis aute irure dolor in.reprehenderit in voluptate velit esse cillum dolore eu fugiat nulla pariatur. Excepteur sint occaecat cupidatat non proident, sunt in culpa qui officia deserunt mollit,</p>
    <p>Lorem ipsum dolor sit amet, consectetur adipiscing sed do eiusmod tempor incididunt labore et dolore magna aliqua. Ut enim Lorem ipsum dolor sit amet, consectetur adipiscing sed do eiusmod tempor incididunt labore et dolore magna aliqua. Ut enim Lorem ipsum aliqua.ipsum</p>
    <p>Lorem ipsum dolor sit amet, consectetur adipiscing sed do eiusmod tempor incididunt labore et dolore magna aliqua. Ut enim ad minim veniam, quis nostrud exercitation ullamco laboris nisi ut aliquip exea commodo consequat.Duis aute irure dolor in reprehenderit in voluptate velit esse cillum irure dolor in reprehenderit in voluptate velit esse irure</p>
    <p>Lorem ipsum dolor sit amet, consectetur adipiscing sed do eiusmod tempor incididunt labore et dolore magna aliqua. Ut enim ad minim veniam, quis nostrud exercitation ullamco laboris nisi ut aliquip exea commodo consequat.Duis aute irure dolor in reprehenderit in voluptate velit esse cillum irure dolor in reprehenderit in voluptate velit esse irure</p>
  </section>

  <svg class="footer-wave" viewBox="0 0 1065 1489" preserveAspectRatio="none" aria-hidden="true">
    <defs>
      <linearGradient id="footerRed" x1="0" y1="0" x2="0" y2="1">
        <stop offset="0" stop-color="var(--red)" style="stop-color:#e21b23"/>
        <stop offset="1" stop-color="var(--red-deep)" style="stop-color:#7c0610"/>
      </linearGradient>
    </defs>
    <path d="M0,1392 C120,1440 260,1462 420,1402 C600,1332 780,1226 920,1225 C980,1225 1030,1236 1065,1250 L1065,1489 L0,1489 Z" fill="url(#footerRed)"/>
    <path d="M304,1425 C500,1398 700,1228 920,1193 C980,1185 1030,1198 1065,1214 L1065,1240 C1030,1226 980,1212 920,1216 C740,1234 520,1392 304,1425 Z" fill="#1e3164"/>
  </svg>

  <footer class="contact">
    <div class="contact-address">1475 Calloway Street,<br>Suite 210, Houston,<br>Texas 77041</div>
    <div class="contact-line">
      <svg viewBox="0 0 24 24"><path d="M6.6 10.8a15.1 15.1 0 0 0 6.6 6.6l2.2-2.2a1 1 0 0 1 1-.25 11.4 11.4 0 0 0 3.6.57 1 1 0 0 1 1 1V20a1 1 0 0 1-1 1A17 17 0 0 1 3 4a1 1 0 0 1 1-1h3.5a1 1 0 0 1 1 1c0 1.25.2 2.45.57 3.57a1 1 0 0 1-.25 1z"/></svg>
      <span>832-361-9027</span>
    </div>
    <div class="contact-line">
      <svg viewBox="0 0 24 24"><path d="M6 2h12v5H6zM4 8h16a2 2 0 0 1 2 2v7h-4v5H6v-5H2v-7a2 2 0 0 1 2-2zm4 8v4h8v-4z"/></svg>
      <span>832-614-7359</span>
    </div>
  </footer>
</main>
</body>
</html>
```